Business Card For Halvenmoor Financial Consulting

Hi, I would like a business card designed. Bold, modern.
Please use the same design as the logo. I have also attached the website design to see the overall theme.
Wordmark Font
Color: Hex: #01AEF7

```html
<!DOCTYPE html>
<html lang="en">
<head>
<meta charset="utf-8">
<title>Halvenmoor Financial Consulting – Business Card</title>
<link rel="stylesheet" href="https://fonts.googleapis.com/css2?family=Open+Sans:wght@400;600;700;800&display=swap">
<style>
  :root {
    --page-bg: #e9edf1;
    --card-navy: #0c4569;
    --card-navy-light: #11517b;
    --card-navy-edge: #0a3a59;
    --accent-blue: #01aef7;
    --accent-soft: #2fa3dc;
    --text-white: #ffffff;
    --text-muted: #d3e2ec;
  }
  * { box-sizing: border-box; margin: 0; padding: 0; }
  html, body {
    width: 1200px; height: 780px; overflow: hidden;
    background: var(--page-bg);
    font-family: "Open Sans", Arial, sans-serif;
  }
  .canvas {
    width: 1200px; height: 780px;
    display: flex; align-items: center; justify-content: center; gap: 40px;
  }
  .card {
    position: relative;
    width: 540px; height: 350px;
    background: var(--card-navy);
    border-radius: 3px;
    box-shadow: 0 3px 0 var(--card-navy-edge), 0 14px 30px rgba(10, 40, 65, 0.28);
    overflow: hidden;
  }

  /* Front side */
  .brand {
    position: absolute; left: 30px; top: 28px;
    display: flex; align-items: center; gap: 10px;
  }
  .brand-square {
    width: 20px; height: 20px;
    border: 2.5px solid var(--accent-blue);
  }
  .brand-name {
    color: var(--text-white);
    font-weight: 700; font-size: 13px;
    letter-spacing: 1.6px; text-transform: uppercase;
    white-space: nowrap;
  }
  .contact {
    position: absolute; left: 30px; top: 120px;
    color: var(--text-muted);
    font-size: 12px; line-height: 1.55;
    list-style: none;
  }
  .contact li { display: flex; align-items: center; gap: 7px; white-space: nowrap; }
  .contact .address { display: block; margin-bottom: 4px; }
  .contact svg { width: 11px; height: 11px; flex: none; }
  .holder {
    position: absolute; right: 44px; top: 92px;
    text-align: right;
  }
  .holder-name {
    font-weight: 800; font-size: 21px; line-height: 1.25;
    color: var(--text-white); letter-spacing: 0.3px;
    white-space: nowrap;
  }
  .holder-name .first { color: var(--accent-soft); }
  .holder-title {
    font-size: 12.5px; color: var(--text-white); margin-top: 2px;
  }
  .accent-tab {
    position: absolute; right: 0; top: 98px;
    width: 16px; height: 34px;
    background: var(--accent-soft);
  }
  .deco-square {
    position: absolute; right: 58px; bottom: -40px;
    width: 210px; height: 210px;
    border: 14px solid var(--card-navy-light);
    box-shadow: inset 0 0 0 1px rgba(255,255,255,0.06), 0 0 0 1px rgba(0,0,0,0.08);
  }

  /* Back side */
  .card--back {
    display: flex; align-items: center; justify-content: center; gap: 18px;
  }
  .back-square {
    width: 54px; height: 54px;
    border: 5px solid var(--accent-blue);
    flex: none;
  }
  .back-name {
    color: var(--text-white);
    font-weight: 700; font-size: 24px; line-height: 1.3;
    letter-spacing: 2.5px; text-transform: uppercase;
    max-width: 330px;
  }
</style>
</head>
<body>
<main class="canvas">

  <section class="card card--front" aria-label="Card front">
    <div class="brand">
      <span class="brand-square"></span>
      <span class="brand-name">Halvenmoor Financial Consulting</span>
    </div>

    <ul class="contact">
      <li class="address">4180 Linden Park Ave. Suite 300<br>Ashford, TX 75210</li>
      <li>
        <svg viewBox="0 0 12 12" aria-hidden="true"><path fill="var(--accent-soft)" d="M2.4 1h2l1 2.6-1.3.9a6.5 6.5 0 0 0 3.4 3.4l.9-1.3L11 7.6v2c0 .8-.6 1.4-1.4 1.4A9.6 9.6 0 0 1 1 2.4C1 1.6 1.6 1 2.4 1z"/></svg>
        (555) 214-6083
      </li>
      <li>
        <svg viewBox="0 0 12 12" aria-hidden="true"><rect x="1" y="2.5" width="10" height="7" rx="1" fill="var(--accent-soft)"/><path d="M1.5 3l4.5 3.4L10.5 3" stroke="var(--card-navy)" stroke-width="1" fill="none"/></svg>
        hello@halvenmoor.com
      </li>
      <li>
        <svg viewBox="0 0 12 12" aria-hidden="true"><circle cx="6" cy="6" r="5" fill="var(--accent-soft)"/><path d="M1 6h10M6 1c-2 2.5-2 7.5 0 10M6 1c2 2.5 2 7.5 0 10" stroke="var(--card-navy)" stroke-width="0.8" fill="none"/></svg>
        www.halvenmoor.com
      </li>
    </ul>

    <span class="deco-square" aria-hidden="true"></span>
    <div class="holder">
      <p class="holder-name"><span class="first">Mira</span> Kovalenko</p>
      <p class="holder-title">Managing Director</p>
    </div>
    <span class="accent-tab"></span>
  </section>

  <section class="card card--back" aria-label="Card back">
    <span class="back-square"></span>
    <p class="back-name">Halvenmoor Financial Consulting</p>
  </section>

</main>
</body>
</html>
```